Willow Cradle Pregnancy and Baby Massage

I need a web design for a new business, WILLOW CRADLE PREGNANCY AND BABY MASSAGE that I am in the process of setting up in the suburbs of Perth, Western Australia. The business is owned and operated by myself and my intention is to service Pregnant Mothers and Parents of Young Babies that would benefit from massage. I would like to have a "Home Page" and pages for "About Me", "Pregnancy Massage", "Baby Massage", a Pricing Page for Pregnancy Massage Sessions, a Pricing Page for Baby Massage Sessions, and a "Contact Me" page to allow clients to either contact me with queries or book available pregnancy massage sessions on a particular day of the week. I would also like a "News" page that would include articles I have written, news about new courses and a link to my Circlet page (yet to be set up). I would like to keep the colour schemes similar to my logo design colours. I need the design to be easy to follow and to appeal to a younger audience (20's to mid 30's).
The target audience is pregnant mothers-to-be wishing to receive massage treatments, and new parents and grandparents of small babies that would like to learn how to massage their babies.
The look and feel should be modern, professional, elegant and feminine.
I need the design to be in a standard format such that I can update the content by myself ( and does not need specialised software) as the company and business progresses.

Target Market(s)

Contact Information for Business Card

Card should have rounded edges. Design should have the same "feel" as the website. Contact Details of my business address, mobile phone, email and website should be included.

Font styles to use
Script

Requirements
Must have
• Same colours as logo design. In cmyk system, the colours are: 20,60,0,0 which best result is pantone 681 and 40,40,0,0 which best result is pantone 2645. Card should include the logo design.

```html
<!DOCTYPE html>
<html lang="en">
<head>
<meta charset="utf-8">
<title>Willow Cradle Pregnancy and Baby Massage – Pregnancy Massage</title>
<link href="https://fonts.googleapis.com/css2?family=Questrial&family=Open+Sans:wght@400;600&display=swap" rel="stylesheet">
<style>
  :root{
    --nav-dark:#3f3d45;
    --footer-dark:#54477a;
    --heading-violet:#7d68ad;
    --title-plum:#a35aa6;
    --logo-plum:#a8559e;
    --text:#2f2f33;
    --lavender:#c3bbdc;
    --pink-soft:#e6c3dc;
    --footer-pink:#f7e6ee;
    --white:#ffffff;
  }
  *{box-sizing:border-box;margin:0;padding:0}
  html,body{width:766px;height:1200px;overflow:hidden;background:var(--white)}
  body{position:relative;font-family:"Questrial",sans-serif;color:var(--text)}
  .top-nav{position:absolute;left:0;top:0;width:766px;height:26px;background:var(--nav-dark);z-index:2}
  .top-nav ul{list-style:none;position:absolute;left:302px;top:8px;display:flex;gap:17px}
  .top-nav a{font-family:"Open Sans",sans-serif;font-size:8px;color:#e6e3ea;text-decoration:none}
  .top-nav a.current{color:#fff;text-decoration:underline}
  .header-waves{position:absolute;left:0;top:26px;z-index:1}
  .brand-card{position:absolute;left:84px;top:-4px;width:180px;height:118px;background:#fff;border-radius:0 0 14px 14px;box-shadow:0 2px 5px rgba(0,0,0,.25);z-index:3}
  .brand-card .frame{position:absolute;left:5px;top:0;right:5px;bottom:5px;border:1px dashed #777;border-top:none;border-radius:0 0 11px 11px}
  .brand-mark{position:absolute;left:78px;top:14px;width:24px;height:24px;border-radius:50%;background:var(--logo-plum)}
  .brand-name{position:absolute;left:0;right:0;top:48px;text-align:center;font-size:17px;line-height:20px;color:var(--logo-plum)}
  .page-title{position:absolute;left:0;width:766px;top:161px;text-align:center;font-size:20px;font-weight:400;color:var(--title-plum)}
  .intro{position:absolute;left:84px;width:598px;top:198px;text-align:center;font-size:12px;line-height:18px}
  .source{position:absolute;left:0;width:766px;top:237px;text-align:center;font-size:8.5px}
  .photo-ring{position:absolute;left:86px;top:293px;width:248px;height:248px;border:1px dashed #555;border-radius:50%}
  .photo{position:absolute;left:9px;top:9px;width:228px;height:228px;border-radius:50%;background:radial-gradient(circle at 40% 65%,#c98a6a 0,#b9876a 30%,#e8e4e2 55%,#f1efee 100%)}
  .benefits{position:absolute;left:383px;top:289px;width:300px}
  h2{font-size:20px;font-weight:400;color:var(--heading-violet)}
  .benefits p{margin-top:10px;font-size:12px;line-height:17.5px}
  ul.points{list-style:none;font-size:12px;line-height:15.5px}
  ul.points li{position:relative;padding-left:12px;margin-bottom:7px}
  ul.points li::before{content:"›";position:absolute;left:0;top:-1px}
  .benefits ul.points{margin-top:8px}
  .safety{position:absolute;left:84px;top:651px;width:600px;font-size:12px;line-height:17.5px}
  .safety p{margin-top:6px}
  .safety p.first{margin-top:10px}
  .safety ul.points{margin-top:8px}
  .safety p.gap{margin-top:30px}
  .footer-band{position:absolute;left:0;top:1037px;width:766px;height:133px;background:radial-gradient(circle at 75% 40%,#f9d3e2 0,var(--footer-pink) 45%,#fbf1f5 100%)}
  .cert-badge{position:absolute;left:90px;top:20px;width:165px;height:92px;border-radius:8px;background:#eedbe8}
  .follow{position:absolute;left:610px;top:47px;width:85px;text-align:center;font-size:9.5px}
  .social{display:flex;align-items:center;justify-content:center;gap:5px;margin-top:7px;font-size:11px;color:var(--footer-dark)}
  .social span.dot{width:14px;height:14px;border-radius:50%;background:var(--footer-dark)}
  .bottom-nav{position:absolute;left:0;top:1170px;width:766px;height:30px;background:var(--footer-dark)}
  .bottom-nav p{text-align:center;margin-top:18px;font-family:"Open Sans",sans-serif;font-size:7.5px;color:#e9e4f2;word-spacing:1px}
</style>
</head>
<body>
  <nav class="top-nav">
    <ul>
      <li><a href="#">Home</a></li>
      <li><a href="#">About Me</a></li>
      <li><a href="#" class="current">Pregnancy Massage</a></li>
      <li><a href="#">Baby Massage</a></li>
      <li><a href="#">Pricing</a></li>
      <li><a href="#">News</a></li>
      <li><a href="#">Contact Me</a></li>
    </ul>
  </nav>
  <svg class="header-waves" width="766" height="100" viewBox="0 0 766 100" aria-hidden="true">
    <path d="M0 0H766V78C700 45 640 20 560 18C470 16 420 70 330 70C250 70 150 60 80 70C40 76 15 85 0 92Z" fill="var(--lavender)" opacity=".85"/>
    <path d="M0 20C90 10 180 30 260 55C330 75 380 40 430 25C520 0 640 10 766 95V0H0Z" fill="var(--pink-soft)" opacity=".7"/>
    <path d="M300 40C420 80 560 85 690 40C720 30 745 25 766 22V0H300Z" fill="#b7aed6" opacity=".55"/>
  </svg>
  <div class="brand-card">
    <div class="frame"></div>
    <span class="brand-mark"></span>
    <p class="brand-name">Willow Cradle<br>Pregnancy and Baby Massage</p>
  </div>

  <h1 class="page-title">Pregnancy Massage</h1>
  <p class="intro">Pregnancy massage is the prenatal use of massage therapy to support the physiological, structural and emotional wellbeing of both mother and baby.</p>
  <p class="source">Source: Evergreen Prenatal Massage Institute</p>

  <div class="photo-ring"><div class="photo" role="img" aria-label="Therapist's hands gently massaging a pregnant belly wrapped in a white towel"></div></div>

  <section class="benefits">
    <h2>Benefits of Pregnancy Massage</h2>
    <p>Pregnancy Massage is a professional relaxation massage that:</p>
    <ul class="points">
      <li>Reduces anxiety caused by hormonal changes</li>
      <li>Improves circulation</li>
      <li>Reduces muscle aches and pain; muscle and joint conditions such as backache, shoulder and neck pain, hip pain, leg cramps, oedema and carpel tunnel</li>
      <li>Relaxes tense muscle, tones loose muscle and increases muscle flexibility.</li>
      <li>Enhances vitality and energy</li>
      <li>Reduces fatigue</li>
      <li>Enhances relaxation and improves sleep patterns as it helps to soothe and relax nervous tension</li>
      <li>Increases circulation to the skin</li>
    </ul>
  </section>

  <section class="safety">
    <h2>Is Pregnancy Massage Safe?</h2>
    <p class="first">Yes, when the massage is performed by a qualified pregnancy massage therapist, who is aware of your medical and obstetric history. It is recommended to align your massage for just after your ante natal check, so that up to date information is available.</p>
    <p>There are times when pregnancy massage is not appropriate.</p>
    <ul class="points">
      <li>The abdomen will not be massaged during the first trimester.</li>
      <li>It is recommended to wait at least one week after amniocentesis, or any invasive procedures.</li>
      <li>If you have a history of blood clots in the legs, any vaginal bleeding, or cramping, pregnancy massage is not recommended.</li>
    </ul>
    <p class="gap">Certain medical or obstetric conditions will require medical clearance from your obstetrician.</p>
    <p>These include;</p>
    <ul class="points">
      <li>Unstable or high blood pressure</li>
      <li>Heart disease</li>
      <li>Placenta praevia</li>
      <li>Cervical incompetence</li>
    </ul>
  </section>

  <footer class="footer-band">
    <div class="cert-badge" role="img" aria-label="Certification badge"></div>
    <div class="follow">
      Follow us on
      <div class="social"><span class="dot"></span>Circlet</div>
    </div>
  </footer>
  <nav class="bottom-nav">
    <p>Home &nbsp;| &nbsp;About Me &nbsp;| &nbsp;Pregnancy Massage &nbsp;| &nbsp;Baby Massage &nbsp;| &nbsp;Pricing &nbsp;| &nbsp;News &nbsp;| &nbsp;Contact Me</p>
  </nav>
</body>
</html>
```